Design the Business card for NetVaultic

Business card required for a professional Cyber Security business.
Company Logo and Icon has already been provided however I would like other options for the logo and icon to compare to. Alternatively, please refine/enhance the image of the logo.icon I have already provided.

If you are going to use the provided logo and icon, I was thinking that the company raised Logo on White background would serve well on the front of the card. See attached. AND, a large company raised stand-alone icon to appear on black background on the back of the card with tagline 'Cyber Risk Management, Governance and Consulting' or 'Cyber Security for your Business' See attached.
Alternatively, provide your own design for the logo and icon.

Target Market(s)

Enterprise, Government, Financial.

Contact Information for Business Card

Tavin Orloweth
Founder and CEO

Email Address
Mobile Number
Website URL
LinkedIn URL

Logo Text

NetVaultic - see attached example of logo

Font styles to use
Other font styles liked:
• Berlin Sans FB

Requirements
Must have
• Clean large and bold icon on the back with tagline.
• Horizontal alignment,
Nice to have
• Round edges.
• Raised Logo/Icon
Should not have
• An unprofessional look and feel.

```html
<!DOCTYPE html>
<html lang="en">
<head>
<meta charset="utf-8">
<title>NetVaultic Business Card</title>
<link rel="stylesheet" href="https://fonts.googleapis.com/css2?family=Fredoka:wght@500&family=Roboto+Condensed:wght@500;700&family=Roboto:wght@400&display=swap">
<style>
  :root {
    --backdrop: #1d1d1f;
    --card-white: #f2f2f2;
    --brand-blue: #1770c4;
    --brand-blue-deep: #2a5bb8;
    --soft-blue: #4f72c8;
    --accent-yellow: #f6c01a;
    --card-dark: #1b1c1e;
    --text-white: #ffffff;
  }
  * { margin: 0; padding: 0; box-sizing: border-box; }
  html, body {
    width: 1200px; height: 960px; overflow: hidden;
    background: var(--backdrop);
  }
  .canvas { position: relative; width: 1200px; height: 960px; }

  .card {
    position: absolute; left: 322px; width: 600px; height: 342px;
    border-radius: 16px; overflow: hidden;
  }
  .card-front { top: 108px; background: var(--card-white); }
  .card-back { top: 494px; background: var(--card-dark); }

  .wordmark {
    position: absolute; display: flex; align-items: center; gap: 14px;
    font-family: "Fredoka", "Trebuchet MS", sans-serif; font-weight: 500;
  }
  .wordmark-dot { border-radius: 50%; background: var(--brand-blue); flex: none; }
  .card-front .wordmark {
    left: 0; right: 0; top: 72px; justify-content: center;
    font-size: 50px; color: var(--brand-blue); line-height: 1;
  }
  .card-front .wordmark-dot { width: 62px; height: 62px; }

  .divider-rule { position: absolute; left: 0; top: 202px; width: 600px; height: 24px; }

  .info-band {
    position: absolute; left: 0; top: 213px; width: 600px; height: 129px;
    background: var(--brand-blue);
  }
  .identity {
    position: absolute; right: 328px; top: 41px; text-align: right;
    font-family: "Roboto Condensed", "Arial Narrow", sans-serif;
  }
  .identity-name {
    color: var(--accent-yellow); font-size: 21px; font-weight: 700; line-height: 26px;
  }
  .identity-role {
    color: var(--text-white); font-size: 15px; font-weight: 500; line-height: 22px;
  }
  .band-separator {
    position: absolute; left: 290px; top: 22px; width: 1px; height: 86px;
    background: rgba(255,255,255,0.7);
  }
  .contact-list {
    position: absolute; left: 308px; top: 26px; list-style: none;
    font-family: "Roboto", Arial, sans-serif; font-size: 14px; color: var(--text-white);
  }
  .contact-list li { display: flex; align-items: center; height: 19px; gap: 8px; }
  .contact-list svg { width: 14px; height: 14px; flex: none; }

  .card-back .wordmark {
    left: 0; right: 0; top: 118px; justify-content: center;
    font-size: 54px; color: var(--soft-blue); line-height: 1;
  }
  .card-back .wordmark-dot { width: 70px; height: 70px; background: var(--soft-blue); }
  .tagline {
    position: absolute; left: 0; right: 0; top: 275px; text-align: center;
    font-family: "Fredoka", "Trebuchet MS", sans-serif; font-weight: 500; font-size: 17px;
    color: var(--soft-blue);
  }
  .tagline .tagline-accent { color: var(--accent-yellow); }
</style>
</head>
<body>
<main class="canvas">
  <section class="card card-front" aria-label="Business card front">
    <div class="wordmark"><span class="wordmark-dot"></span><span>NetVaultic</span></div>

    <svg class="divider-rule" viewBox="0 0 600 24" aria-hidden="true">
      <line x1="10" y1="12" x2="590" y2="12" stroke="#2a5bb8" stroke-width="3"/>
      <circle cx="10" cy="12" r="6.5" fill="#f2f2f2" stroke="#2a5bb8" stroke-width="2"/>
      <circle cx="588" cy="12" r="6.5" fill="#f2f2f2" stroke="#2a5bb8" stroke-width="2"/>
    </svg>

    <div class="info-band">
      <div class="identity">
        <div class="identity-name">TAVIN ORLOWETH</div>
        <div class="identity-role">FOUNDER &amp; CEO</div>
      </div>
      <div class="band-separator"></div>
      <ul class="contact-list">
        <li>
          <svg viewBox="0 0 14 14" aria-hidden="true"><rect x="3.5" y="0.5" width="7" height="13" rx="1.5" fill="#f6c01a"/><rect x="5" y="2" width="4" height="8" fill="#1770c4"/></svg>
          555 014 2290
        </li>
        <li>
          <svg viewBox="0 0 14 14" aria-hidden="true"><rect x="1" y="3" width="12" height="8.5" fill="#f6c01a"/><path d="M1 3.5 L7 8 L13 3.5" fill="none" stroke="#1770c4" stroke-width="1.2"/></svg>
          tavin@netvaultic.com
        </li>
        <li>
          <svg viewBox="0 0 14 14" aria-hidden="true"><circle cx="7" cy="7" r="6" fill="#f6c01a"/><path d="M1 7 H13 M7 1 C4 4 4 10 7 13 M7 1 C10 4 10 10 7 13" fill="none" stroke="#1770c4" stroke-width="1"/></svg>
          www.netvaultic.com
        </li>
        <li>
          <svg viewBox="0 0 14 14" aria-hidden="true"><circle cx="7" cy="7" r="6" fill="#f6c01a"/></svg>
          netvaultic
        </li>
      </ul>
    </div>
  </section>

  <section class="card card-back" aria-label="Business card back">
    <div class="wordmark"><span class="wordmark-dot"></span><span>NetVaultic</span></div>
    <p class="tagline">Cyber Risk Management, <span class="tagline-accent">Governance &amp; Consulting</span></p>
  </section>
</main>
</body>
</html>
```